Web design for new streaming audio service

We need a homepage design for a new streaming audio service. Our company is called Dunmoral, and we’re basically Vexlo for Audiobooks, Stand-Up Comedy, Lectures, Language Learning, etc. Essentially like Plumtrek for everything audio EXCEPT music.
You don’t have to code the homepage (Design Only), but it should include 3 different designs to work with 1) Web; 2) Phones; 3) Tablets.
Below is a link to a mockup of the web version which gives a good idea of what elements we want. This is just a mockup and we want you to improve it.
Once you download the mockup, please refer to the more detailed instructions below:
The following outlines the design project for the Dunmoral homepage. We have provided a rough mockup of the homepage layout that gives you a general idea of what we’re going for. There are a few elements that we are attached to, and many others where you have complete creative freedom to do whatever you think looks good.
The ZIP file includes the following:
* Mockup to see what we have in mind (dunmoral-homepage-mockup.jpg)
* Text used (dunmoral-homepage-text.txt)
* Raw image of actor (dunmoral-actor1.jpg)
* Raw images for samples (dunmoral-sample-[name].jpg)
Although we have only provided a mockup layout for the web version, we also need you to provide a mobile phone and a tablet version of the design also. It’s very possible the tablet version may be substantially similar to the web version, but the mobile phone version will likely be much different.
All of the raw files are included in the attached ZIP file. Please use our photographs and text as provided although cropping, sizing, etc. is flexible per the instructions below.
Display Requirements:
* Web Version - Minimum resolution 1024x768 (72 dpi) but should look good on 1920x1080 (72 dpi) - Page should be designed to scale to look acceptable in all resolutions in between.
* Phone Version - Minimum Zarno 4 - 640x960 (326 dpi) but should look good on Harlow Quasar T5 - 1920x1080 (441 dpi) - Page should be designed to scale to look acceptable in all resolutions and devices in between.
* Tablet Version - Minimum Bristly Ember QX 7” - 1280x800 (216 dpi) but should also look good on a Tavo Breeze - 2048x1536 (264 dpi) - Page should be designed to scale to look acceptable in all resolutions and devices in between.
Above the Fold - We want to make sure the Dunmoral logo, Member Login Link, Large Photo, Headline, Price, Button, and the first row of sample images are all “Above the fold”. As a general guideline, this means 600 pixels high on a 1024x768 72 dpi web screen. This requirement is less important on Phone versions.
Top Logo Bar - We want to retain the blue bar with the Dunmoral logo on the page, although we are open to a different size, shape and positioning if it greatly enhances the design. Please use the standard logo color, although you are welcome to use either the horizontal or vertical orientation of the logo based on your design.
Text color, font and size - Feel free to design the text in anyway you choose as long as the text is readable on the target platforms.
Buttons - Feel free to use any size, shape and colors for the buttons as long as they are obvious and clickable relative to the page. The only exception is the Chatterly button should follow the Chatterly color scheme and logo treatment (the mockup doesn’t seem 100% correct.)
Top Photograph - We want to retain the large photograph across the top of the screen although final shape and dimensions are flexible.
Size and shape of content samples (i.e. Audiobooks, Stand-Up Comedy, etc.) - Feel free to design the content samples in anyway you choose.
Three Sales Points (i.e. Listen on your Zarno…, All you can enjoy…, etc.) - The Three Sales Points are envisioned to each have a corresponding illustration which you should provide and have rights for. The placeholder is represented by a square next to the text. The color size and shape of these elements are flexible and can be designed in any way you choose.
Opt-in form - Feel free to design the opt-in form in anyway you choose as long as the text is readable and the interactivity is obvious on the target platforms.
Text links and copyright notice - Feel free to design the bottom of the page text links and copyright notice in anyway you choose.
Additional colors, graphic design elements, etc. - Feel free to use any additional colors, graphic design elements, etc. to support your design.
people who want to listen to audio through their mobile devices.
Graphic Design

```html
<!DOCTYPE html>
<html lang="en">
<head>
<meta charset="utf-8">
<title>Dunmoral – Unlimited Listening</title>
<link href="https://fonts.googleapis.com/css2?family=Ubuntu:wght@400;500&family=Source+Sans+3:wght@400;600&display=swap" rel="stylesheet">
<style>
:root{
  --blue:#2f8fc6;
  --blue-light:#6ec0ea;
  --blue-tile:#5db6e6;
  --orange:#f7941d;
  --green:#2e9a12;
  --ink:#3c3c3c;
  --grey:#777;
  --nav:#6b6d70;
  --form-bg:#f2f2f2;
  --footer:#3e3e3e;
  --chat:#3b5a9a;
}
*{margin:0;padding:0;box-sizing:border-box}
html,body{width:787px;height:1200px;overflow:hidden;background:#fff}
body{position:relative;font-family:"Source Sans 3",sans-serif;color:var(--ink)}
.abs{position:absolute}

.logo{left:88px;top:20px;display:flex;align-items:center;gap:6px;font:500 18px "Ubuntu",sans-serif;color:#3f5567}
.logo-dot{width:14px;height:14px;border-radius:50%;background:var(--blue)}
.login-btn{left:598px;top:32px;width:104px;height:27px;background:var(--blue-light);border:1px solid #4aa6d6;border-radius:2px;color:#fff;font-size:9.5px;display:flex;align-items:center;justify-content:center;gap:6px}

.hero{left:0;top:96px;width:787px;height:325px;background:linear-gradient(100deg,#5a4b3f 0%,#a58a72 22%,#d9c7b6 42%,#efece9 62%,#f6f6f6 100%)}
.nav{left:85px;top:77px;width:617px;height:31px;background:linear-gradient(#7a7c80,#5e6064);border-radius:2px;display:flex;align-items:center;padding-left:10px;gap:0;box-shadow:0 2px 4px rgba(0,0,0,.2)}
.nav a{color:#fff;font-size:9px;text-decoration:none;padding:5px 14px;border-radius:2px}
.nav a.active{background:var(--blue-light);padding:5px 14px}

.headline{right:85px;top:166px;text-align:right;font:500 28px/34px "Ubuntu",sans-serif;color:#3a3a3a}
.price{right:85px;top:250px;font-size:16px;color:#3a3a3a}
.price b{font:500 22px "Ubuntu",sans-serif;color:var(--green)}
.cta{left:570px;top:294px;width:131px;height:32px;background:var(--orange);border-radius:2px;color:#fff;font-size:11.5px;display:flex;align-items:center;justify-content:center}
.note{right:87px;top:334px;font-size:8.5px;color:#555}
.dots{left:345px;top:397px;width:98px;height:24px;background:#fff;clip-path:polygon(16% 0,84% 0,100% 100%,0 100%);display:flex;gap:4px;align-items:center;justify-content:center;padding-top:4px}
.dots i{width:9px;height:9px;border-radius:50%;background:#e2e2e2;display:block}
.dots i.on{background:var(--blue-light)}

.sec-title{left:0;width:787px;top:457px;text-align:center;font:400 18px "Ubuntu",sans-serif;color:#444}
.sec-desc{left:140px;width:507px;top:489px;text-align:center;font-size:8.5px;line-height:13px;color:var(--grey)}

.tile{width:220px;display:flex;gap:13px}
.cover{width:78px;height:78px;flex:none}
.tile h3{font:400 11.5px "Ubuntu",sans-serif;color:var(--blue);margin:1px 0 6px}
.tile p{font-size:8.5px;line-height:13px;color:var(--grey);width:105px}

.point{width:198px;height:82px;background:var(--blue-tile);border:1px solid #4ba8da;color:#fff;padding:10px 11px}
.point .head{display:flex;gap:9px;align-items:flex-start;font-size:11px;line-height:14px;min-height:32px}
.point p{font-size:8.5px;line-height:13px;margin-top:6px}
.point svg{flex:none}

.form-band{left:0;top:998px;width:787px;height:138px;background:var(--form-bg);border-top:1px solid #e4e4e4}
.trial-title{left:86px;top:1019px;font:400 16px "Ubuntu",sans-serif;color:var(--blue)}
.trial-text{left:86px;top:1047px;width:235px;font-size:8.5px;line-height:14px;color:#555}
.trial-note{left:85px;top:1103px;font-size:8.5px;color:#444}
.label{font-size:8.5px;color:var(--blue)}
.field{width:187px;height:26px;background:#fff;border:1px solid #e0e0e0;font-size:8.5px;font-style:italic;color:#aaa;padding:7px 11px}
.access{left:559px;top:1037px;width:140px;height:26px;background:linear-gradient(#666,#4a4a4a);color:#fff;font-size:9.5px;display:flex;align-items:center;justify-content:center;border-radius:1px}
.or{left:559px;width:140px;top:1073px;text-align:center;font-size:8.5px;color:#555}
.chat-btn{left:559px;top:1092px;width:140px;height:26px;background:var(--chat);color:#fff;font-size:9px;font-weight:600;display:flex;align-items:center;gap:8px;padding-left:6px;border-radius:2px}
.chat-btn i{width:16px;height:16px;background:#fff;opacity:.9;display:block}

.footer{left:0;top:1136px;width:787px;height:64px;background:var(--footer);color:#fff;text-align:center;font-size:8px}
.footer .links{margin-top:21px}
.footer .links span{margin:0 6px;color:#bbb}
.footer .copy{margin-top:10px}
</style>
</head>
<body>

<div class="abs logo"><span class="logo-dot"></span>Dunmoral</div>
<div class="abs login-btn">
  <svg width="8" height="10" viewBox="0 0 8 10"><rect x="0" y="4" width="8" height="6" fill="#2d6f98"/><path d="M2 4V2.5a2 2 0 0 1 4 0V4" stroke="#2d6f98" fill="none" stroke-width="1.3"/></svg>
  Member Login
</div>

<div class="abs hero" role="img" aria-label="Smiling young man wearing headphones, listening on his phone"></div>

<nav class="abs nav">
  <a class="active">Home</a><a>About</a><a>Help</a><a>Contact Us</a><a>Member Login</a><a>Privacy Policy</a><a>Terms of Service</a>
</nav>

<h1 class="abs headline">Unlimited Listening<br>Wherever you are</h1>
<div class="abs price">Only <b>$9.99</b> per month</div>
<div class="abs cta">Start Your Free Trial !</div>
<div class="abs note">*Credit Card Not Required</div>
<div class="abs dots"><i class="on"></i><i></i><i></i><i></i></div>

<h2 class="abs sec-title">A sample of what you can listen to on Dunmoral</h2>
<p class="abs sec-desc">Dunmoral is a new service that gives you unlimited access to the world's largest library of streaming audio via your computer and mobile devices. new service that gives you unlimited access to the world's largest library.</p>

<div class="abs tile" style="left:85px;top:546px"><div class="cover" role="img" aria-label="Audiobook cover" style="background:linear-gradient(#2a2f3a,#0e1420)"></div><div><h3>Audiobooks</h3><p>Dunmoral is a new service that gives you unlimited access to the world's largest library.</p></div></div>
<div class="abs tile" style="left:295px;top:546px"><div class="cover" role="img" aria-label="Stand-up comedy album cover" style="background:linear-gradient(#8a7c6c,#c9a86a)"></div><div><h3>Stand-Up Comedy</h3><p>Dunmoral is a new service that gives you unlimited access to the world's largest library.</p></div></div>
<div class="abs tile" style="left:505px;top:546px"><div class="cover" role="img" aria-label="French language course cover" style="background:linear-gradient(#1b86c9,#0f4f8a)"></div><div><h3>Language Learning</h3><p>Dunmoral is a new service that gives you unlimited access to the world's largest library.</p></div></div>

<div class="abs tile" style="left:85px;top:652px"><div class="cover" role="img" aria-label="Memoir cover" style="background:linear-gradient(#c7b59a,#8fb467)"></div><div><h3>Biographies &amp; Memoirs</h3><p>Dunmoral is a new service that gives you unlimited access to the world's largest library.</p></div></div>
<div class="abs tile" style="left:295px;top:652px"><div class="cover" role="img" aria-label="Relaxation meditation cover" style="background:linear-gradient(#b04fa8,#4d2f6e)"></div><div><h3>Guided Meditations</h3><p>Dunmoral is a new service that gives you unlimited access to the world's largest library.</p></div></div>
<div class="abs tile" style="left:505px;top:652px"><div class="cover" role="img" aria-label="Business training cover" style="background:linear-gradient(#5a3a24,#151a30)"></div><div><h3>Business Training</h3><p>Dunmoral is a new service that gives you unlimited access to the world's largest library.</p></div></div>

<div class="abs tile" style="left:85px;top:760px"><div class="cover" role="img" aria-label="Celebrity interview cover" style="background:linear-gradient(#b07a7e,#3a2a2a)"></div><div><h3>Celebrity Interviews</h3><p>Dunmoral is a new service that gives you unlimited access to the world's largest library.</p></div></div>
<div class="abs tile" style="left:295px;top:760px"><div class="cover" role="img" aria-label="Fitness workout cover" style="background:linear-gradient(#2fa6d8,#d8463c)"></div><div><h3>Fitness Programs</h3><p>Dunmoral is a new service that gives you unlimited access to the world's largest library.</p></div></div>
<div class="abs tile" style="left:505px;top:760px"><div class="cover" role="img" aria-label="Meditation guide cover" style="background:linear-gradient(#3b7fc4,#dfe9f0)"></div><div><h3>Med Programs</h3><p>Dunmoral is a new service that gives you unlimited access to the world's largest library.</p></div></div>

<div class="abs point" style="left:85px;top:883px">
  <div class="head"><svg width="22" height="20" viewBox="0 0 22 20"><rect x="1" y="1" width="14" height="18" rx="1" fill="none" stroke="#2a5f80" stroke-width="2"/><rect x="12" y="7" width="9" height="12" rx="1" fill="var(--blue-tile)" stroke="#2a5f80" stroke-width="2"/></svg>Listen on your Zarno, Slatepad or Droidex device.</div>
  <p>Dunmoral is a new service that gives you unlimited access to the world's largest library.</p>
</div>
<div class="abs point" style="left:295px;top:883px">
  <div class="head"><svg width="20" height="22" viewBox="0 0 20 22"><rect x="1" y="1" width="18" height="20" fill="#2a5f80"/><path d="M5 6h3M5 11h3M5 16h3M11 6h5M11 11h5M11 16h5" stroke="#fff" stroke-width="1.6"/></svg>All you can enjoy for one low monthly price.</div>
  <p>Dunmoral is a new service that gives you unlimited access to the world's largest library.</p>
</div>
<div class="abs point" style="left:505px;top:883px">
  <div class="head"><svg width="22" height="20" viewBox="0 0 22 20"><path d="M11 1L21 19H1Z" fill="#2a5f80"/><path d="M11 7v6" stroke="#fff" stroke-width="2"/><circle cx="11" cy="16" r="1.2" fill="#fff"/></svg>No obligation. Cancel any time.</div>
  <p>Dunmoral is a new service that gives you unlimited access to the world's largest library.</p>
</div>

<section class="abs form-band"></section>
<h2 class="abs trial-title">Start Your Free Trial</h2>
<p class="abs trial-text">You will get instant &amp; unlimited access to all the material on Dunmoral for 14 days. There is no obligation &amp; you can cancel at any time.</p>
<p class="abs trial-note">*Credit Card Not Required for Free Trial</p>

<div class="abs label" style="left:348px;top:1022px">User Name :</div>
<div class="abs field" style="left:348px;top:1037px">Enter your Name...</div>
<div class="abs label" style="left:348px;top:1077px">Email - Id :</div>
<div class="abs field" style="left:348px;top:1092px">Enter your Email Id...</div>

<div class="abs access">Get Instant Access &nbsp;&gt;&gt;</div>
<div class="abs or">OR</div>
<div class="abs chat-btn"><i></i>Sign Up Using Chatterly</div>

<footer class="abs footer">
  <div class="links">About<span>|</span>Help<span>|</span>Contact Us<span>|</span>Member Login<span>|</span>Privacy Policy<span>|</span>Terms of Service</div>
  <div class="copy">Copyright ©2014 Dunmoral LLC - All Rights Reserved</div>
</footer>

</body>
</html>
```